Coastline Premier Retreats Business Card Design

Design a business card for Coastline Premier Retreats. Look at the website for colors and reference. Card should have logo, name, title, office number, mobile number, email, URL and a tagline like, "Luxury Hotel & Resort Email Marketing" (This might change).

https://www.coastlinepremierretreats.example

The rest I will leave up to your imagination.

Contact Information for Business Card

Logo, name, title, office number, mobile number, email, URL and a tagline like, "Luxury Hotel & Resort Email Marketing" (This might change).

```html
<!DOCTYPE html>
<html lang="en">
<head>
<meta charset="UTF-8">
<title>Coastline Premier Retreats – Business Card</title>
<link rel="stylesheet" href="https://fonts.googleapis.com/css2?family=Montserrat:wght@300;400;700;800&family=Open+Sans:ital,wght@1,400&display=swap">
<style>
  :root {
    --page-bg: #2a2a2a;
    --card-bg: #1b1b1b;
    --accent: #f07a1a;
    --text-light: #f2f2f2;
    --text-muted: #d6d6d6;
    --mark-faint: #3a3a3a;
  }
  * { margin: 0; padding: 0; box-sizing: border-box; }
  html, body {
    width: 1200px; height: 900px; overflow: hidden;
    background: var(--page-bg);
    font-family: "Montserrat", sans-serif;
  }
  .sheet {
    width: 1200px; height: 900px;
    display: flex; flex-direction: column;
    align-items: center; justify-content: center; gap: 36px;
  }
  .card {
    position: relative;
    width: 700px; height: 400px;
    background: var(--card-bg);
    box-shadow: 0 14px 30px rgba(0,0,0,.45);
  }

  /* Front */
  .brand {
    position: absolute; left: 150px; top: 52px;
    display: flex; align-items: center; gap: 14px;
  }
  .brand-square {
    width: 22px; height: 22px; background: var(--accent);
  }
  .brand-name {
    color: var(--text-light);
    font-weight: 800; font-size: 24px; letter-spacing: 1px;
    text-transform: uppercase;
  }
  .person { position: absolute; left: 60px; top: 175px; }
  .person-name {
    color: var(--accent); font-weight: 800; font-size: 30px;
    letter-spacing: 1px; text-transform: uppercase;
  }
  .person-title {
    color: var(--text-muted); font-weight: 300; font-size: 15px; margin-top: 2px;
  }
  .contact {
    position: absolute; left: 360px; top: 220px;
    color: var(--text-light); font-size: 14px; line-height: 1.55;
  }
  .address { margin: 0 0 10px 22px; }
  .contact-row { display: flex; align-items: center; gap: 8px; }
  .contact-row svg { width: 14px; height: 14px; fill: var(--accent); flex: none; }
  .url-domain { color: var(--accent); }

  /* Back */
  .back-mark {
    position: absolute; left: 0; right: 0; top: 120px;
    text-align: center;
    color: var(--mark-faint);
    font-weight: 800; font-size: 40px; letter-spacing: 2px;
    text-transform: uppercase;
  }
  .tagline {
    position: absolute; right: 70px; bottom: 90px;
    color: var(--accent);
    font-family: "Open Sans", sans-serif; font-style: italic; font-size: 22px;
  }
</style>
</head>
<body>
<main class="sheet">
  <section class="card card-front">
    <div class="brand">
      <span class="brand-square"></span>
      <span class="brand-name">Coastline Premier Retreats</span>
    </div>
    <div class="person">
      <h1 class="person-name">Marcus Hale</h1>
      <p class="person-title">CEO/Founder</p>
    </div>
    <div class="contact">
      <p class="address">Po Box, 48 Harbor Lane<br>Seaview Bay, CA 90000</p>
      <p class="contact-row">
        <svg viewBox="0 0 16 16" aria-hidden="true"><path d="M4 0h8a1 1 0 0 1 1 1v14a1 1 0 0 1-1 1H4a1 1 0 0 1-1-1V1a1 1 0 0 1 1-1zm1 2v10h6V2zm3 11a1 1 0 1 0 0 2 1 1 0 0 0 0-2z"/></svg>
        555.014.2200
      </p>
      <p class="contact-row">
        <svg viewBox="0 0 16 16" aria-hidden="true"><path d="M1 5c0-2 3-3 7-3s7 1 7 3v1h-4V4.5H5V6H1zM3 7h10l2 7H1zm5 1.5a2 2 0 1 0 0 4 2 2 0 0 0 0-4z"/></svg>
        +34 600 000 123
      </p>
      <p class="contact-row">
        <svg viewBox="0 0 16 16" aria-hidden="true"><path d="M1 3h14v10H1zm1.5 1.5L8 9l5.5-4.5v-.2h-11z"/></svg>
        info@coastlinepremierretreats.example
      </p>
      <p class="contact-row">
        <svg viewBox="0 0 16 16" aria-hidden="true"><path d="M8 0a8 8 0 1 0 0 16A8 8 0 0 0 8 0zm0 1.5c.8 0 1.8 1.7 2.1 4.5H5.9C6.2 3.2 7.2 1.5 8 1.5zM1.6 7h2.8c0 .7 0 1.4.1 2H1.6a6.5 6.5 0 0 1 0-2zm4.3 3h4.2c-.3 2.8-1.3 4.5-2.1 4.5S6.2 12.8 5.9 10zm5.7-1c.1-.6.1-1.3.1-2h2.7a6.5 6.5 0 0 1 0 2z"/></svg>
        www.<span class="url-domain">coastlinepremierretreats</span>.example
      </p>
    </div>
  </section>

  <section class="card card-back">
    <div class="back-mark">Coastline Premier Retreats</div>
    <p class="tagline">Luxury Hotel &amp; Resort Email Marketing</p>
  </section>
</main>
</body>
</html>
```